Window Cleaning Leaflet

Hi everyone,

I need a leaflet (couldn't find 'leaflet' as an option when begining this project - so one sided only) to send out to coastal properties in South side Melbourne. The Flyer is aimed at high net individuals, mummies, business people etc who own these properties who don't have time to clean the windows themselves (often multiple levels) and want their home looking fabulous in time for Christmas and NY's celebrations.

I would really love a new and original design for a window washing leaflet. something outside of the norm that 'pops' and makes people feel happy when they look at it.

I guess a point of differentiation is that I'm a female working in a mans industry so appeal to mothers looking for someone who is 'reliable, trustworthy and understanding of peoples needs'.

I have made an outline of what I would like included in the leaflet, so if you could please take a look, feel free to change things around, wording and layout etc. If you can make it sound more professional please do so.

I would like the colours to be 'happy' colours, maybe with a silly season theme?

Overall aesthetically pleasing is a must, I find most window cleaning leaflets fairly mundane and boring, please feel free to think outside the box. The more original the better.

Target Market(s)

People who own large Melbourne homes in affluent suburbs, mainly suburbs with a lot of large coastal properties. Generally owned by high net worth individuals who just don't have tme to clean the windows themselves due to their profession or hectic lifestyles but can afford to pay someone else to do it.

Industry/Entity Type

Window Cleaning

Requirements
Must have
• 1) The name of the business - Kelda’s Window Washing Services
• 2) The coupon special and all details attached:
• Small Homes (up to 12 windows) $120
• Medium Homes (up to 16 windows) $180
• Large Homes (up to 20 windows, 2 storeys) $240
• 20% discount
• *Discount applicable to first time customers only.
• *All services include fly screen, sill and tracks cleaned as well as cobweb removal.
• *Houses with more than 20 windows (or two levels) will have an immediate quote provided upon inspection of the property with 20% discount applied.
• *Kelda’s Window Washing Services are fully insured.
• 3) My contact number - 0418 265 903

```html
<!DOCTYPE html>
<html lang="en">
<head>
<meta charset="utf-8">
<title>Kelda’s Window Washing Services – Leaflet</title>
<link rel="stylesheet" href="https://fonts.googleapis.com/css2?family=Open+Sans:ital,wght@0,400;0,600;0,700;0,800;1,700;1,800&display=swap">
<style>
  :root {
    --red: #d7232a;
    --red-dark: #9e1519;
    --blue: #1f8fd6;
    --blue-box: #2a7fc4;
    --orange: #f5861f;
    --green: #5cb133;
    --white: #ffffff;
    --ink: #333333;
    --sky-top: #6f8fb8;
    --sky-mid: #c9d7e8;
    --room: #8a6a4e;
  }
  * { box-sizing: border-box; margin: 0; padding: 0; }
  html, body { width: 849px; height: 1200px; overflow: hidden; background: #eeeeee; }
  body { font-family: "Open Sans", Arial, sans-serif; }
  .leaflet { position: relative; width: 849px; height: 1200px; background: var(--white); overflow: hidden; }

  .hero-scene {
    position: absolute; left: 0; top: 0; width: 849px; height: 762px;
    background:
      linear-gradient(180deg, rgba(230,60,60,.85) 0%, rgba(250,190,40,.7) 9%, rgba(90,170,220,.6) 16%, transparent 24%),
      radial-gradient(ellipse at 50% 55%, var(--sky-mid) 0%, var(--sky-top) 45%, transparent 70%),
      linear-gradient(90deg, var(--room) 0%, #c9b59d 18%, #9fb4cf 50%, #c9b59d 82%, var(--room) 100%);
  }

  .title-ribbon { position: absolute; left: 185px; top: 14px; width: 480px; height: 104px; }
  .title-ribbon svg { position: absolute; inset: 0; }
  .title-ribbon h1 {
    position: absolute; inset: 0; display: flex; flex-direction: column; justify-content: center;
    text-align: center; color: var(--white); font-weight: 800; font-size: 32px; line-height: 1.08;
    letter-spacing: .5px; text-transform: uppercase; padding-bottom: 6px;
  }

  .price-list { position: absolute; left: 274px; top: 133px; }
  .price-row { display: flex; height: 56px; margin-bottom: 24px; box-shadow: 0 2px 6px rgba(0,0,0,.25); }
  .price-row.large { height: 74px; }
  .price-row .amount {
    width: 122px; color: var(--white); font-weight: 800; font-size: 42px;
    display: flex; align-items: center; justify-content: center; letter-spacing: -1px;
  }
  .price-row .amount sup { font-size: 20px; margin-right: 2px; align-self: flex-start; margin-top: 8px; }
  .price-row .label {
    width: 230px; background: rgba(255,255,255,.92); padding: 4px 12px;
    display: flex; flex-direction: column; justify-content: center; color: var(--ink);
  }
  .price-row .label strong { font-size: 19px; font-weight: 700; line-height: 1.1; }
  .price-row .label span { font-size: 14px; font-weight: 600; line-height: 1.2; }
  .price-row.small .amount { background: var(--blue); }
  .price-row.medium .amount { background: var(--orange); }
  .price-row.large .amount { background: var(--green); }
  .price-row.small .label strong { color: var(--blue); }
  .price-row.medium .label strong { color: var(--orange); }
  .price-row.large .label strong { color: var(--green); }

  .promise-box {
    position: absolute; left: 269px; top: 461px; width: 481px; padding: 12px 16px;
    background: rgba(31,127,196,.9); color: var(--white); font-weight: 700; font-size: 20px; line-height: 1.3;
  }
  .service-note {
    position: absolute; left: 500px; top: 604px; width: 250px; text-align: right;
    color: var(--white); font-weight: 600; font-size: 17px; line-height: 1.4;
    text-shadow: 0 1px 3px rgba(0,0,0,.5);
  }

  .offer { position: absolute; left: 40px; top: 775px; width: 570px; }
  .offer h2 { color: var(--red); font-weight: 800; font-style: italic; font-size: 27px; line-height: 1.2; }
  .offer .phone { color: var(--red); font-weight: 800; font-size: 32px; margin: 6px 0 12px; }
  .terms { list-style: none; }
  .terms li { position: relative; padding-left: 24px; font-size: 16px; line-height: 1.38; color: var(--ink); margin-bottom: 8px; }
  .terms li::before { content: ""; position: absolute; left: 0; top: 6px; width: 11px; height: 11px; background: var(--red); }

  .gift-scene {
    position: absolute; left: 623px; top: 764px; width: 226px; height: 436px;
    background: radial-gradient(ellipse at 55% 70%, #e8343a 0%, #c41d24 45%, rgba(196,29,36,.3) 70%, transparent 80%);
  }
  .discount-badge { position: absolute; left: 690px; top: 790px; width: 118px; height: 118px; }
  .discount-badge svg { position: absolute; inset: 0; }
  .badge-text {
    position: absolute; inset: 0; display: flex; flex-direction: column; align-items: center; justify-content: center;
    color: var(--red); font-weight: 800; line-height: .95;
  }
  .badge-pct { display: block; font-size: 38px; letter-spacing: -1px; }
  .badge-off { display: block; font-size: 24px; letter-spacing: 2px; }
</style>
</head>
<body>
<main class="leaflet">
  <div class="hero-scene" role="img" aria-label="Open white window frame with festive bunting above, blue sky with clouds beyond and a squeegee wiping the glass"></div>

  <header class="title-ribbon">
    <svg width="480" height="104" viewBox="0 0 480 104" aria-hidden="true">
      <polygon points="0,28 40,28 40,96 0,96 18,62" fill="var(--red-dark)"/>
      <polygon points="480,28 440,28 440,96 480,96 462,62" fill="var(--red-dark)"/>
      <path d="M30 8 Q240 -6 450 8 L450 90 Q240 76 30 90 Z" fill="var(--red)"/>
    </svg>
    <h1><span>Kelda’s Window</span><span>Washing Services</span></h1>
  </header>

  <section class="price-list">
    <div class="price-row small">
      <div class="amount"><sup>$</sup>120</div>
      <div class="label"><strong>Small Homes</strong><span>(up to 12 windows)</span></div>
    </div>
    <div class="price-row medium">
      <div class="amount"><sup>$</sup>180</div>
      <div class="label"><strong>Medium Homes</strong><span>(up to 16 windows)</span></div>
    </div>
    <div class="price-row large">
      <div class="amount"><sup>$</sup>240</div>
      <div class="label"><strong>Large Homes</strong><span>(up to 20 windows, 2 storeys)</span></div>
    </div>
  </section>

  <p class="promise-box">Kelda understands and wants to help you enjoy your home looking its best before Christmas and NY’s celebrations begin!</p>

  <p class="service-note">We provide a reliable, professional service, ensuring that your home will sparkle</p>

  <section class="offer">
    <h2>Call Kelda today and take advantage of our special introductory offer.</h2>
    <p class="phone">Kelda – 0418 265 903</p>
    <ul class="terms">
      <li>Discount applicable to first time customers only.</li>
      <li>All services include fly screen, sill and tracks cleaned as well as cobweb removal.</li>
      <li>Houses with more than 20 windows (or two levels) will have an immediate quote provided upon inspection of the property with 20% discount applied.</li>
      <li>Kelda’s Window Washing Services are fully insured.</li>
    </ul>
  </section>

  <div class="gift-scene" role="img" aria-label="Pile of red wrapped Christmas gifts with ribbons and a Santa hat"></div>
  <div class="discount-badge">
    <svg width="118" height="118" viewBox="0 0 118 118" aria-hidden="true">
      <circle cx="59" cy="59" r="56" fill="var(--white)" stroke="var(--red)" stroke-width="3"/>
    </svg>
    <div class="badge-text"><span class="badge-pct">20%</span><span class="badge-off">OFF</span></div>
  </div>
</main>
</body>
</html>
```